Looking to Redesign Brevonix.com website

You guys did one of the brochures for brevonix.com and I would like to see if we can go ahead and get an estimate for a redesigned web site for the company. We currently have a couple of pages on brevonix.com which are very much a starter type site.

The new design will need to reflect some of the things discussed in the brochure. It will have flash. Needs to be designed for simple hosting using cpanels.

The site needs to have between 12 and 15 pages with flash pages to move through features. Integrated with twitter like it is now, and contact forms delivered from our CRM along with other interactive features such as subscription to newsletter, etc...

I don't have lots of details on how to proceed yet, but here are some competitor sites:

Can we take a look at potential costs involved in the redo of the site as vague as my description above can permit.

Target Market(s)

Business to Business

Number of Pages Required

5+ page

Font styles to use
Sans Serif

Requirements
Must have
• Must have professional feel. Similar to brochure. and logo.
• Include our story in the discussion.
• embedded links to our CRM for popup contact forms.
• Logo files and 2 types of brochures uploaded.
• Important to keep color scheme
Nice to have
• Flash and some movement
Should not have
• Not sure yet

```html
<!DOCTYPE html>
<html lang="en">
<head>
<meta charset="utf-8">
<title>Brevonix – Case Studies</title>
<link href="https://fonts.googleapis.com/css2?family=Raleway:wght@400;500;600;700&family=Russo+One&display=swap" rel="stylesheet">
<style>
:root{
  --red:#b50a0f;
  --red-dark:#7d0306;
  --ink:#222;
  --text:#555;
  --muted:#888;
  --white:#fff;
  --footer-top:#4a4a4a;
  --footer-bottom:#2a2a2a;
  --bar:#333;
  --photo-blue:#2e5873;
}
*{margin:0;padding:0;box-sizing:border-box}
html,body{width:1200px;height:2211px;overflow:hidden;background:var(--white)}
body{position:relative;font-family:"Raleway",Arial,sans-serif;color:var(--text)}
.abs{position:absolute}

/* header */
.brand{left:75px;top:62px;display:flex;align-items:center;gap:10px}
.brand-dot{width:46px;height:46px;border-radius:50%;background:var(--red)}
.brand-name{font-family:"Raleway",Arial,sans-serif;font-weight:700;font-size:24px;color:var(--red)}
.contact{top:30px;display:flex;align-items:center;gap:14px}
.contact-label{font-size:9px;letter-spacing:.5px;color:var(--muted);text-transform:uppercase}
.contact-value{font-size:13px;font-weight:700;color:#333;text-transform:uppercase;margin-top:2px}
.contact-value.phone{font-size:17px;text-transform:none}
.sep{top:34px;width:1px;height:36px;background:#ddd}
.nav{top:96px;right:64px;display:flex;align-items:center;gap:8px;list-style:none}
.nav li{font-size:12.5px;font-weight:700;color:#333;padding:10px 19px;border-radius:18px;letter-spacing:.3px}
.nav li.active{background:var(--red);color:var(--white)}

/* hero */
.hero{left:0;top:147px;width:1200px;height:380px;background:linear-gradient(100deg,#6f8ea3 0%,#3d6682 35%,var(--photo-blue) 60%,#1f3d52 100%)}
.hero-wave{left:0;top:400px}

/* case studies */
.section-title{left:75px;top:570px;display:flex;align-items:center;gap:18px}
.section-title .mark{width:36px;height:36px;border-radius:50%;background:#bbb}
.section-title h1{font-family:"Russo One",Arial,sans-serif;font-style:italic;font-size:27px;color:var(--red);letter-spacing:.5px}
.case-photo{width:326px;height:326px;border-radius:50%;box-shadow:0 10px 0 0 #3a3a3a, 0 5px 0 0 var(--red);border:3px solid var(--red)}
.case-text{width:660px}
.case-text h2{font-family:"Russo One",Arial,sans-serif;font-style:italic;font-size:20px;color:var(--ink);margin-bottom:20px}
.case-text p{font-size:14.8px;line-height:27.6px;color:var(--text)}

/* footer */
.footer-wave{left:0;top:1700px}
.footer-bg{left:0;top:1880px;width:1200px;height:260px;background:linear-gradient(var(--footer-top),#333)}
.footer-brand{left:75px;top:1925px;display:flex;align-items:center;gap:10px}
.footer-brand .brand-dot{background:var(--white)}
.footer-brand .brand-name{color:var(--white)}
.footer-about{left:75px;top:2018px;width:300px;font-size:14px;line-height:25px;color:#e6e6e6}
.read-more{left:75px;top:2077px;font-size:13.5px;font-weight:700;color:var(--white)}
.footer-divider{top:1915px;width:2px;height:190px;background:#2b2b2b;box-shadow:1px 0 0 #555}
.footer-heading{font-size:13.5px;font-weight:700;color:var(--white);letter-spacing:1px}
.quick-links{left:466px;top:1956px;display:grid;grid-template-columns:165px 150px;row-gap:11px;list-style:none}
.quick-links li{font-size:13.5px;color:#e6e6e6}
.field{left:835px;width:291px;height:38px;border-radius:19px;background:var(--white);font-size:13.5px;color:#666;padding:11px 24px}
.signup{left:1011px;top:2056px;width:115px;height:37px;border-radius:19px;background:linear-gradient(var(--red),var(--red-dark));color:var(--white);font-size:13.5px;font-weight:700;text-align:center;line-height:37px;box-shadow:0 3px 6px rgba(0,0,0,.4)}
.bottom-bar{left:0;top:2138px;width:1200px;height:73px;background:linear-gradient(#3a3a3a,var(--footer-bottom))}
.copyright{left:75px;top:2166px;font-size:12.5px;color:#bbb}
.social{top:2160px;width:30px;height:30px;border-radius:50%}
</style>
</head>
<body>

<header>
  <div class="abs brand"><span class="brand-dot"></span><span class="brand-name">brevonix</span></div>

  <div class="abs contact" style="left:510px">
    <svg width="30" height="32" viewBox="0 0 30 32"><circle cx="15" cy="10" r="7" fill="#333"/><path d="M3 32c0-8 5-13 12-13s12 5 12 13z" fill="#333"/></svg>
    <div><div class="contact-label">Support</div><div class="contact-value">Chat with us</div></div>
  </div>
  <div class="abs sep" style="left:684px"></div>
  <div class="abs contact" style="left:705px">
    <svg width="28" height="22" viewBox="0 0 28 22"><rect x="1.5" y="1.5" width="25" height="19" rx="2" fill="none" stroke="#333" stroke-width="2.5"/><path d="M2 3l12 10 12-10" fill="none" stroke="#333" stroke-width="2.5"/></svg>
    <div><div class="contact-label">Email us at</div><div class="contact-value">sales@brevonix.com</div></div>
  </div>
  <div class="abs sep" style="left:936px"></div>
  <div class="abs contact" style="left:955px">
    <svg width="18" height="28" viewBox="0 0 18 28"><path d="M4 2l5 1 1 6-4 2c1 4 3 7 6 9l3-3 3 3-1 5c-8 0-15-10-15-20z" fill="#333"/></svg>
    <div><div class="contact-label">Call us now</div><div class="contact-value phone">8005550147</div></div>
  </div>

  <ul class="abs nav">
    <li>HOME</li><li>WHY BREVONIX</li><li>BENEFITS</li><li class="active">CASE STUDIES</li><li>HARDWARE</li><li>ABOUT US</li>
  </ul>
</header>

<div class="abs hero" role="img" aria-label="Hand holding a magnifying glass over a blue background with the words case study"></div>
<svg class="abs hero-wave" width="1200" height="140" viewBox="0 0 1200 140">
  <path d="M0 42C250 0 520 40 760 70S1080 100 1200 95V140H0Z" fill="#111"/>
  <path d="M0 32C250 -8 520 30 760 62S1080 92 1200 86V96C1080 100 960 90 760 72S250 8 0 46Z" fill="var(--red)"/>
  <path d="M0 50C250 10 520 45 760 78S1080 110 1200 106V140H0Z" fill="#fff"/>
</svg>

<main>
  <div class="abs section-title"><span class="mark"></span><h1>CASE STUDIES</h1></div>

  <div class="abs case-photo" style="left:75px;top:647px;background:linear-gradient(135deg,#dfe6ec,#9aa3aa 60%,#555)" role="img" aria-label="Desk office telephone with a display screen"></div>
  <div class="abs case-text" style="left:466px;top:703px">
    <h2>LOREM IPSUM DOLOR SIT AMET,</h2>
    <p>Aliquam molestie, mi et imperdiet euismod, dui purus auctor tellus, et interdum lacus lectus et ante. Sed accumsan sollicitudin sapien, sit amet adipiscing turpis gravida ac. In congue, neque ac lobortis volutpat, libero mauris varius mi, vitae suscipit ipsum ligula vitae risus. Duis aliquam nibh a dui iaculis viverra id a velit. Vivamus egestas risus in magna varius commodo. Sed semper viverra egestas. Etiam pretium porttitor lectus, vel ornare neque porta volutpat.</p>
  </div>

  <div class="abs case-text" style="left:75px;top:1089px">
    <h2>LOREM IPSUM DOLOR SIT AMET,</h2>
    <p>Aliquam molestie, mi et imperdiet euismod, dui purus auctor tellus, et interdum lacus lectus et ante. Sed accumsan sollicitudin sapien, sit amet adipiscing turpis gravida ac. In congue, neque ac lobortis volutpat, libero mauris varius mi, vitae suscipit ipsum ligula vitae risus. Duis aliquam nibh a dui iaculis viverra id a velit. Vivamus egestas risus in magna varius commodo. Sed semper viverra egestas. Etiam pretium porttitor lectus, vel ornare neque porta volutpat.</p>
  </div>
  <div class="abs case-photo" style="left:798px;top:1032px;background:linear-gradient(135deg,#8a9aa8,#c7ccd0 45%,#3f74b5)" role="img" aria-label="Hand plugging a network cable into a switch panel"></div>

  <div class="abs case-photo" style="left:75px;top:1370px;background:linear-gradient(135deg,#4d8fc4,#1d4f86 55%,#0f2a4a)" role="img" aria-label="Laptop in a server room showing a monitoring chart"></div>
  <div class="abs case-text" style="left:466px;top:1425px">
    <h2>LOREM IPSUM DOLOR SIT AMET,</h2>
    <p>Aliquam molestie, mi et imperdiet euismod, dui purus auctor tellus, et interdum lacus lectus et ante. Sed accumsan sollicitudin sapien, sit amet adipiscing turpis gravida ac. In congue, neque ac lobortis volutpat, libero mauris varius mi, vitae suscipit ipsum ligula vitae risus. Duis aliquam nibh a dui iaculis viverra id a velit. Vivamus egestas risus in magna varius commodo. Sed semper viverra egestas. Etiam pretium porttitor lectus, vel ornare neque porta volutpat.</p>
  </div>
</main>

<footer>
  <svg class="abs footer-wave" width="1200" height="190" viewBox="0 0 1200 190">
    <path d="M0 10C300 60 700 110 1200 110V190H0Z" fill="var(--red)"/>
    <path d="M0 45C300 75 700 160 1200 165V190H0Z" fill="#1a1a1a"/>
    <path d="M0 58C300 88 700 172 1200 178V190H0Z" fill="var(--footer-top)"/>
  </svg>
  <div class="abs footer-bg"></div>

  <div class="abs footer-brand"><span class="brand-dot"></span><span class="brand-name">brevonix</span></div>
  <p class="abs footer-about">Inter-Company Cloud Communications Platform...</p>
  <div class="abs read-more">Read More</div>

  <div class="abs footer-divider" style="left:437px"></div>
  <div class="abs footer-heading" style="left:466px;top:1925px">QUICK LINKS</div>
  <ul class="abs quick-links">
    <li>Home</li><li>Hardware</li>
    <li>Why Brevonix</li><li>About Us</li>
    <li>Benefits</li><li>Contact Us</li>
    <li>Case Studies</li>
  </ul>

  <div class="abs footer-divider" style="left:810px"></div>
  <div class="abs footer-heading" style="left:839px;top:1925px">NEWSLETTER SIGN UP</div>
  <div class="abs field" style="top:1960px">Enter Name</div>
  <div class="abs field" style="top:2005px">Enter Email Address</div>
  <div class="abs signup">SIGN UP</div>

  <div class="abs bottom-bar"></div>
  <div class="abs copyright">© 2015-2016 brevonix. All Rights Reserved.</div>
  <span class="abs social" style="left:983px;background:#3b5a9a"></span>
  <span class="abs social" style="left:1020px;background:#2aa3df"></span>
  <span class="abs social" style="left:1057px;background:#1c7bb5"></span>
  <span class="abs social" style="left:1094px;background:#f08a1d"></span>
</footer>

</body>
</html>
```